Revamp Of Landing Page For an Automated AI Voice Agents Agency

here is my current landing page https://app.brightfernpromotionhub.biz/v2/preview/WXKRPmQ4hLzYBvNdTeGS?notrack=true

Please use all my current content and imagery of ai agents in your new design. Make it easy to ready, easy to navigate and easy to understand

I am looking for a SLEEK shiny polished looking website. I like Dark themed sites but am open to see light themed sites too so please dont be shy.

The site should have an Ai Voice Agent Theme about it. Maybe look and feel of futureistic but simple and not intimidating to the average person...

Here are a couple website designs I like for reference:
https://q7v.io/
https://ai-bots.marekholvin.com/
https://chatwelmo.com/ai-agents

Target Market(s)

b2b

Industry/Entity Type

AI Voice Agents

Coding

Coded - Design and coding required

Font styles to use
Other font styles liked:
• open

Requirements
Must have
• all elements and content and images used in existing design.
Nice to have
• open
Should not have
• open

```html
<!DOCTYPE html>
<html lang="en">
<head>
<meta charset="utf-8">
<title>BrightFern Promotion Hub – AI Voice Agents</title>
<link href="https://fonts.googleapis.com/css2?family=Poppins:ital,wght@0,400;0,500;0,600;0,700;0,800;1,400;1,500&display=swap" rel="stylesheet">
<style>
:root{
  --navy:#17168c;
  --navy-deep:#0c0b5e;
  --navy-card:#1d1fa6;
  --navy-line:#3a3fd0;
  --yellow:#f8b51a;
  --yellow-text:#f5b21c;
  --white:#ffffff;
  --soft:#d9dcff;
  --muted:#b9bce8;
  --blue-card:#2a5fd0;
  --green-card:#1e8c4d;
  --orange-card:#d2581f;
  --purple-card:#8b2bd4;
  --red-card:#c3283c;
}
*{margin:0;padding:0;box-sizing:border-box}
html,body{width:1200px;height:5146px;overflow:hidden}
body{font-family:"Poppins",sans-serif;color:var(--white);background:var(--navy)}
section,footer{position:relative;width:1200px;overflow:hidden}
.abs{position:absolute}
.btn{position:absolute;display:flex;align-items:center;justify-content:center;background:var(--yellow);color:#1b1b8f;font-weight:700;font-size:21px;border-radius:3px;text-decoration:none}
.fine{position:absolute;font-style:italic;font-size:12.5px;line-height:24px;color:var(--white)}
.illus{position:absolute}

/* hero */
.hero{height:720px;background:linear-gradient(100deg,#1b1e9e 0%,#2228b6 45%,#2c3bd0 70%,#1a2fa5 100%)}
.hero .illus{right:0;top:0;width:540px;height:720px;background:radial-gradient(ellipse at 55% 40%,#7fa6ff 0%,#3b5ee0 35%,rgba(34,40,182,0) 75%)}
.brand{position:absolute;left:76px;top:26px;display:flex;align-items:center;gap:14px}
.brand-dot{width:44px;height:44px;border-radius:50%;background:var(--white)}
.brand-name{font-size:30px;font-weight:600;letter-spacing:1px}
.hero h1{position:absolute;left:75px;top:215px;width:590px;font-size:30px;line-height:39px;font-weight:800}

/* workforce */
.workforce{height:1460px;background:var(--navy)}
.section-title{position:absolute;left:0;width:1200px;text-align:center;font-weight:800;font-size:48px;line-height:58px}
.card{position:absolute;border-radius:6px;overflow:hidden;padding:32px 16px}
.card h3{font-size:32px;line-height:34px;font-weight:700}
.card .tag{font-size:14px;font-weight:700;line-height:24px;margin-top:14px}
.card p{font-size:13.5px;line-height:26px;margin-top:14px}
.card .illus{border-radius:40px}
.c-sales{left:75px;top:188px;width:512px;height:336px;background:linear-gradient(135deg,#2563cd,#2a46b0)}
.c-recep{left:615px;top:188px;width:513px;height:336px;background:linear-gradient(135deg,#1b8f4c,#27a35a)}
.c-lead{left:75px;top:550px;width:1053px;height:334px;background:linear-gradient(135deg,#c6501c,#e0742c)}
.c-appt{left:75px;top:912px;width:512px;height:336px;background:linear-gradient(135deg,#7d25cf,#a438de)}
.c-follow{left:615px;top:912px;width:513px;height:336px;background:linear-gradient(135deg,#b8223a,#d23a48)}

/* wish */
.wish{height:430px;background:linear-gradient(90deg,#1a1b96 0%,#1c1f8c 45%,#11105e 100%)}
.wish .illus{right:0;top:0;width:560px;height:430px;background:radial-gradient(ellipse at 50% 50%,#5a72d8 0%,#2b3aa0 40%,rgba(20,20,100,0) 75%)}
.h-big{font-weight:800;font-size:48px;line-height:50px}
.gold{color:var(--yellow-text);font-weight:700}

/* employee */
.employee{height:490px;background:var(--navy)}
.feat{position:absolute;top:195px;width:329px;height:215px;background:var(--navy-card);border:1px solid var(--navy-line);border-radius:4px;text-align:center}
.feat svg{margin-top:24px}
.feat h4{font-size:21px;font-weight:600;margin-top:10px}
.feat p{font-size:13.5px;line-height:24px;color:var(--soft);margin-top:4px}

/* hire */
.hire{height:490px;background:linear-gradient(90deg,#101070,#17178a 60%,#14137a)}
.hire .illus{left:95px;top:40px;width:310px;height:400px;border-radius:150px 150px 40px 40px;background:radial-gradient(ellipse at 50% 40%,#e3e6f2 0%,#8e95b8 45%,rgba(30,30,120,0) 75%)}

/* faq */
.faq{height:490px;background:linear-gradient(180deg,#1a1b98,#1b1c95)}
.faq-item{position:absolute;left:75px;width:655px;font-size:19px}
.faq-line{position:absolute;left:75px;width:655px;height:1px;background:#4448c4}
.faq-icon{position:absolute;right:0;top:4px;width:18px;height:18px;border-radius:50%;background:var(--white)}
.review{position:absolute;left:793px;top:78px;width:334px;height:348px;background:var(--navy-card);border:1px solid var(--navy-line);border-radius:4px;text-align:center;padding-top:32px}
.review h4{font-size:29px;line-height:39px;font-weight:700}

/* promise */
.promise{height:275px;background:linear-gradient(90deg,#1d1fa4,#1b1c9a)}
.pcard{position:absolute;top:45px;height:190px;background:var(--navy-card);border:1px solid var(--navy-line);border-radius:4px;text-align:center}
.pcard h4{font-size:19px;line-height:27px;font-weight:600;margin-top:10px}
.pcard p{font-size:13.5px;line-height:20px;color:var(--soft)}

/* cta */
.cta{height:445px;background:linear-gradient(180deg,#0c0c55,#0a0a4a)}

/* footer */
.footer{height:346px;background:#0d0c5c;text-align:center;font-size:12.5px;line-height:24px;color:var(--soft)}
</style>
</head>
<body>

<section class="hero">
  <div class="illus" role="img" aria-label="Glossy blue humanoid robot wearing a headset microphone"></div>
  <div class="brand"><span class="brand-dot"></span><span class="brand-name">BrightFern Promotion Hub</span></div>
  <h1>Ai Voice Agents That Answer Calls, Book Appts, Send Emails, Text Messages, Follow Up Reminders, Transfer Calls &amp; More For You 24 Hours 7 Days A Week!</h1>
  <a class="btn" href="#" style="left:75px;top:440px;width:420px;height:48px">Get An Instant Free Demo</a>
  <p class="fine" style="left:75px;top:508px;width:620px">We Will Create An Ai Agent Customized For Your Business At No Cost. Simply Click The Button Above And Your Very Own Ai Agent Will Be Calling You In Just A Couple Minutes. Experience The Magic And Get Ready To Be Very Impressed!</p>
</section>

<section class="workforce">
  <h2 class="section-title" style="top:72px">Meet Your New AI-Powered Workforce</h2>

  <article class="card c-sales">
    <h3>Ai Sales<br>Agent</h3>
    <p style="width:300px;margin-top:22px">Brian will take your inbound sales calls. Will give all detailed information to the customer, answer questions in a normal conversational tone and can book sales appointments or transfer hot prospects to a human to close the sale.</p>
    <div class="illus" role="img" aria-label="Purple cartoon robot with glowing eyes" style="right:10px;top:40px;width:180px;height:280px;background:radial-gradient(ellipse,#a46df0,#6a3cc8 55%,rgba(42,70,176,0) 80%)"></div>
  </article>

  <article class="card c-recep">
    <h3>Ai Receptionist</h3>
    <div class="tag" style="width:320px">Takes Overflow and After Hours Calls or Can Take Calls 24/7 &amp; Transfer To Appropriate Dept.</div>
    <p style="width:320px;margin-top:10px">Cody handles all your calls 24/7. You can also set him to only take overflow calls and after hours. He can send emails and sms messages and even book appointments over the call</p>
    <div class="illus" role="img" aria-label="White cartoon robot with a speech bubble" style="right:0;top:20px;width:170px;height:300px;background:radial-gradient(ellipse,#f2f5f7,#b9d6c6 50%,rgba(39,163,90,0) 80%)"></div>
  </article>

  <article class="card c-lead">
    <h3 style="margin-top:40px">Ai Lead Qualifier</h3>
    <div class="tag" style="margin-top:10px">Conversate With Prospects To Qualify Before Handing Over To Sales Team</div>
    <p style="width:600px;margin-top:10px">All of our ai agents gather information and qualify leads. If they are interested in the services on the call then our ai agents will assist them with booking an appointment with our sales team over the call.</p>
    <div class="illus" role="img" aria-label="Orange cartoon robot sitting in a chair with a laptop and chat bubbles" style="right:40px;top:10px;width:360px;height:310px;background:radial-gradient(ellipse,#f49a3a,#b5561e 55%,rgba(224,116,44,0) 80%)"></div>
  </article>

  <article class="card c-appt">
    <h3>Ai Appointment<br>Setter</h3>
    <div class="tag" style="width:260px;font-size:13.5px;line-height:22px">Book Appts &amp; Reservations On Auto Pilot</div>
    <p style="width:270px;margin-top:12px">Bobby offers business advice, helps brainstorm ideas, and provides insights on growth tactics to support your entrepreneurial journey.</p>
    <div class="illus" role="img" aria-label="White robot working on a laptop" style="right:0;top:10px;width:230px;height:320px;background:radial-gradient(ellipse,#eef0f5,#c28be8 50%,rgba(164,56,222,0) 80%)"></div>
  </article>

  <article class="card c-follow">
    <h3>Ai Follow Up<br>Reminders</h3>
    <div class="tag" style="width:230px;font-size:13.5px;line-height:24px">Calls, Sends SMS &amp; Email Reminders</div>
    <p style="width:320px;margin-top:12px">Sam handles all the follow up calls, appt reminders and sends out the email and sms reminders too.</p>
    <div class="illus" role="img" aria-label="White robot with a chat bubble" style="right:10px;top:20px;width:190px;height:300px;background:radial-gradient(ellipse,#eef0f5,#dd8c96 50%,rgba(210,58,72,0) 80%)"></div>
  </article>

  <a class="btn" href="#" style="left:388px;top:1298px;width:424px;height:48px">Get An Instant Free Demo</a>
  <p class="fine" style="left:150px;top:1366px;width:900px;text-align:center">We Will Create An Ai Agent Customized For Your Business At No Cost. Simply Click The Button Above And Your Very Own Ai Agent Will Be Calling You In Just A Couple Minutes. Experience The Magic And Get Ready To Be Very Impressed!</p>
</section>

<section class="wish">
  <div class="illus" role="img" aria-label="Silver humanoid robot holding a smartphone"></div>
  <h2 class="abs h-big" style="left:75px;top:58px;width:560px">Your Wish Is Their Command</h2>
  <p class="abs gold" style="left:75px;top:170px;font-size:24px">Install the power of AI for your business</p>
  <p class="abs" style="left:75px;top:210px;width:560px;font-size:24px;line-height:34px">Your New Ai Agents Will Never Call In Sick And Will Never Complain!</p>
  <p class="abs" style="left:75px;top:286px;width:600px;font-size:13.5px;line-height:25px">With your new team of AI Agents, handling inbound calls, sending emails and sms messages, booking appointments and handling customer service inquiries is going to save you a ton of time and money.</p>
</section>

<section class="employee">
  <h2 class="section-title" style="top:50px;line-height:60px">An Employee<br>That Never Gets Sick!</h2>
  <div class="feat" style="left:75px">
    <svg width="60" height="60" viewBox="0 0 60 60" fill="none" stroke="#fff" stroke-width="2"><circle cx="30" cy="30" r="20"/><path d="M30 10v40M15 22h30M15 38h30M22 14v32M38 14v32"/></svg>
    <h4>Trained In Seconds</h4><p>Learns Your Entire Website<br>In Seconds</p>
  </div>
  <div class="feat" style="left:436px">
    <svg width="60" height="60" viewBox="0 0 60 60" fill="none" stroke="#fff" stroke-width="2"><circle cx="30" cy="30" r="20"/><ellipse cx="30" cy="30" rx="9" ry="20"/><path d="M10 30h40M13 20h34M13 40h34"/></svg>
    <h4>Worldwide</h4><p>Works Anywhere In The Globe</p>
  </div>
  <div class="feat" style="left:798px">
    <svg width="60" height="60" viewBox="0 0 60 60" fill="none" stroke="#fff" stroke-width="2.5" stroke-linecap="round"><circle cx="27" cy="20" r="10"/><path d="M10 50c0-10 8-17 17-17M36 44l6 6 10-12"/></svg>
    <h4>User-Friendly</h4><p>Your Ai Agents Sound As If They're<br>Real Humans</p>
  </div>
</section>

<section class="hire">
  <div class="illus" role="img" aria-label="Small white robot with glowing blue eyes holding a tablet"></div>
  <h2 class="abs h-big" style="left:433px;top:52px;line-height:56px">Our Ai Agents<br>Our Ready To Be Hired</h2>
  <p class="abs gold" style="left:433px;top:180px;font-size:24px">Lightning-Fast Responses</p>
  <p class="abs" style="left:433px;top:218px;width:560px;font-size:24px;line-height:34px">Instant answers, no coffee, bathroom or lunch breaks needed.</p>
  <a class="btn" href="#" style="left:433px;top:296px;width:423px;height:48px">Get An Instant Free Demo</a>
  <p class="fine" style="left:433px;top:364px;width:690px">We Will Create An Ai Agent Customized For Your Business At No Cost. Simply Click The Button Above And Your Very Own Ai Agent Will Be Calling You In Just A Couple Minutes. Experience The Magic And Get Ready To Be Very Impressed!</p>
</section>

<section class="faq">
  <h2 class="abs" style="left:75px;top:62px;font-size:48px;font-weight:800">Do You Have Questions?</h2>
  <div class="faq-item" style="top:148px;color:var(--yellow-text)">What exactly are the AI Voice Agents?<span class="faq-icon" style="background:var(--yellow)"></span></div>
  <p class="fine" style="left:75px;top:192px;width:560px;line-height:24px">AI Voice Agents are specialized human sounding bots, having smart and masterful conversations and each is expertly trained in seconds for a specific business function.</p>
  <div class="faq-line" style="top:288px"></div>
  <div class="faq-item" style="top:308px">How will these AI Voice Agents benefit?<span class="faq-icon"></span></div>
  <div class="faq-line" style="top:356px"></div>
  <div class="faq-item" style="top:378px">Are they easy to use?<span class="faq-icon"></span></div>
  <div class="review">
    <h4>After Our<br>Customers Have<br>A Conversation<br>With Their New Ai<br>Voice Agent They<br>Give Us 5 Stars!</h4>
    <svg width="220" height="36" viewBox="0 0 220 36" style="margin-top:8px" fill="#f8b51a">
      <g id="star"><path d="M18 2l4.7 10.5 11.3 1-8.6 7.5 2.6 11.2L18 26.3 8 32.2l2.6-11.2L2 13.5l11.3-1z"/></g>
      <use href="#star" x="44"/><use href="#star" x="88"/><use href="#star" x="132"/><use href="#star" x="176"/>
    </svg>
  </div>
</section>

<section class="promise">
  <h2 class="abs" style="left:75px;top:110px;font-size:48px;line-height:56px;font-weight:800">Our Promise<br>To You</h2>
  <div class="pcard" style="left:497px;width:298px">
    <svg width="44" height="44" viewBox="0 0 44 44" fill="none" stroke="#fff" stroke-width="2.5" style="margin-top:40px"><rect x="5" y="8" width="34" height="31" rx="4"/><path d="M5 17h34M14 4v8M30 4v8"/><g fill="#fff" stroke="none"><rect x="12" y="22" width="5" height="4"/><rect x="20" y="22" width="5" height="4"/><rect x="28" y="22" width="5" height="4"/><rect x="12" y="30" width="5" height="4"/><rect x="20" y="30" width="5" height="4"/></g></svg>
    <h4>14-day money-back<br>guarantee*</h4>
  </div>
  <div class="pcard" style="left:827px;width:300px">
    <svg width="50" height="44" viewBox="0 0 50 44" fill="none" stroke="#fff" stroke-width="2.5" style="margin-top:40px"><path d="M6 20c0-9 8-15 18-15s18 6 18 15-8 15-18 15c-3 0-5 0-8-1L6 38l3-8c-2-3-3-6-3-10z"/><path d="M15 21h18"/></svg>
    <h4 style="margin-top:6px">24/7 Customer Support</h4>
    <p>Often praised for our friendly<br>&amp; helpful support team.</p>
  </div>
</section>

<section class="cta">
  <h2 class="section-title" style="top:72px;line-height:56px">These AI Agents Can Help Your<br>Business Tremendously. Imagine The<br>Possibilities</h2>
  <a class="btn" href="#" style="left:388px;top:273px;width:424px;height:48px">Get An Instant Free Demo</a>
  <p class="fine" style="left:70px;top:334px;width:1060px;text-align:center">We Will Create An Ai Agent Customized For Your Business At No Cost. Simply Click The Button Above And Your Very Own Ai Agent Will Be Calling You In Just A Couple Minutes. Experience The Magic And Get Ready To Be Very Impressed!</p>
</section>

<footer class="footer">
  <p style="padding-top:62px">© 2025 VoxaLoop Systems</p>
  <p>*14-Day Money Back Guarantee Terms: If you use the ai agents and you're not happy. Then you can contact us in the first 14 days for a full refund.</p>
  <p>DISCLAIMER:</p>
  <p style="margin-top:38px">PRIVACY | TERMS &amp; CONDITIONS | EARNINGS &amp; PRODUCTS DISCLAIMER</p>
  <p>Do you have questions about ( ) Please email ( )</p>
  <p style="margin-top:38px">IMPORTANT: This site is not a part of the Friendverse website or Friendverse Inc. Additionally, this site is NOT endorsed by Friendverse in any way.</p>
  <p>FRIENDVERSE is a trademark of FRIENDVERSE, Inc.</p>
</footer>

</body>
</html>
```